Corporate travel agency website design

Hello I need a website design that will look professional. I want that anyone that gos on our site understands that we are a large successful company. I want it to be up to par with other large companies. The site should be sleek and neat.
Below I will attach my logo. A recent one page add I made and content for my add that will be used for the website.

```html
<!DOCTYPE html>
<html lang="en">
<head>
<meta charset="utf-8">
<title>Norvelle Travel — Business Travel Reinvented</title>
<link href="https://fonts.googleapis.com/css2?family=Montserrat:wght@800;900&family=Mulish:wght@400;600;700&family=Ubuntu:wght@500;700&display=swap" rel="stylesheet">
<style>
:root{
  --navy:#0a1a3c;
  --navy-soft:#1f2d4d;
  --sky:#cfeaf8;
  --accent:#6cc7ef;
  --ink:#3a3f4a;
  --muted:#5b6270;
  --grey-bg:#f2f3f7;
  --footer:#050505;
  --footer-bar:#1c1c1c;
  --white:#ffffff;
}
*{margin:0;padding:0;box-sizing:border-box}
html,body{width:1200px;height:3978px;overflow:hidden}
body{position:relative;background:var(--white);font-family:"Mulish",sans-serif;color:var(--ink)}
.abs{position:absolute}
a{color:inherit;text-decoration:none}

/* header */
.site-header{position:absolute;left:0;top:0;width:1200px;height:127px;background:var(--white)}
.topbar{position:absolute;left:0;top:0}
.brand{position:absolute;left:100px;top:48px;display:flex;align-items:center;gap:10px;white-space:nowrap}
.brand-dot{width:24px;height:24px;border-radius:50%;background:var(--navy)}
.brand-name{font-weight:700;font-size:18px;color:var(--navy);letter-spacing:1px}
.top-mail{position:absolute;left:520px;top:6px;display:flex;align-items:center;gap:8px;color:var(--white);font-size:12px;white-space:nowrap}
.top-mail .ic{width:24px;height:24px;border-radius:50%;background:var(--white);display:flex;align-items:center;justify-content:center}
.top-phone{position:absolute;left:872px;top:0;width:230px;height:38px;background:var(--white);display:flex;align-items:center;gap:8px;padding-left:12px;font-size:12px;color:var(--navy);white-space:nowrap}
.top-phone .ic{width:26px;height:26px;border-radius:50%;background:var(--navy);display:flex;align-items:center;justify-content:center}
.nav-link{position:absolute;top:75px;font-size:12px;font-weight:600;color:var(--navy);white-space:nowrap;display:flex;align-items:center;gap:6px}
.nav-cta{position:absolute;left:948px;top:61px;width:147px;height:43px;border-radius:22px;background:var(--navy);color:var(--white);font-size:13px;font-weight:700;display:flex;align-items:center;justify-content:center;gap:16px}

/* hero */
.hero{position:absolute;left:0;top:127px;width:1200px;height:715px}
.hero-title{position:absolute;left:113px;top:310px;font-family:"Montserrat",sans-serif;font-weight:900;font-size:58px;color:var(--navy);letter-spacing:-1px;line-height:1;white-space:nowrap}
.hero-sub{position:absolute;left:115px;top:393px;font-weight:600;font-size:26px;letter-spacing:4.5px;color:var(--navy);white-space:nowrap}
.btn-outline{position:absolute;border:2px solid var(--navy);border-radius:22px;color:var(--navy);font-size:13px;font-weight:700;display:flex;align-items:center;justify-content:center;gap:14px;background:rgba(255,255,255,.25)}
.arrow-btn{position:absolute;width:58px;height:58px;border-radius:50%;background:var(--white);display:flex;align-items:center;justify-content:center;box-shadow:0 2px 8px rgba(0,0,0,.1)}
.dots{position:absolute;left:572px;top:768px;display:flex;gap:8px}
.dots span{width:12px;height:12px;border-radius:50%;border:2px solid var(--navy-soft)}
.dots span.on{border-color:var(--accent);background:var(--accent)}

/* headings */
.h-sec{font-family:"Ubuntu",sans-serif;font-weight:700;font-size:36px;color:var(--navy);white-space:nowrap}
.h-sec .light{color:#3b4150;font-weight:500}
.rule{display:flex;align-items:center;gap:4px}
.rule i{display:block;height:3px;background:var(--navy)}
.rule b{display:block;width:18px;height:3px;background:var(--accent)}

/* why */
.why-visual{position:absolute;left:90px;top:934px;width:500px;height:490px;border-radius:40px;background:linear-gradient(160deg,#5a6070,#4a3f35 55%,#2c2f3a)}
.why-text{position:absolute;left:613px;top:1013px;width:472px;font-size:15px;line-height:24.7px;text-align:justify;color:var(--muted)}
.btn-solid{position:absolute;background:var(--navy);color:var(--white);border-radius:22px;font-size:13px;font-weight:700;display:flex;align-items:center;justify-content:center;gap:14px}

/* services */
.services{position:absolute;left:0;top:1513px;width:1200px;height:1400px;background:var(--grey-bg)}
.svc-card{position:absolute;left:127px;width:906px;height:324px;border-radius:162px;background:var(--sky)}
.svc-title{position:absolute;font-family:"Ubuntu",sans-serif;font-weight:500;font-size:24px;color:var(--navy);white-space:nowrap}
.svc-text{position:absolute;font-size:15px;line-height:24px;color:var(--muted)}
.svc-photo{position:absolute;width:268px;height:268px;border-radius:50%;border:3px solid var(--navy)}
.svc-ring{position:absolute;width:300px;height:300px;border-radius:50%;border:2px solid var(--navy)}
.under{position:absolute;height:3px;width:54px;background:var(--navy)}

/* contact */
.contact{position:absolute;left:0;top:2840px;width:1200px;height:716px}
.c-kicker{position:absolute;left:666px;top:2958px;font-size:17px;color:var(--muted)}
.c-title{position:absolute;left:661px;top:2985px;font-family:"Ubuntu",sans-serif;font-weight:700;font-size:40px;color:var(--navy)}
.c-text{position:absolute;left:658px;top:3052px;width:400px;font-size:16px;line-height:25px;color:var(--muted)}
.field{position:absolute;left:658px;width:395px;height:42px;background:var(--navy);border-radius:4px;color:#d9e2f2;font-size:12.5px;padding:15px 18px 0}

/* footer */
.footer{position:absolute;left:0;top:3556px;width:1200px;height:350px;background:var(--footer);color:var(--white)}
.f-div{position:absolute;top:0;width:1px;height:258px;background:#2b2b2b}
.f-head{position:absolute;top:90px;font-weight:700;font-size:17px;letter-spacing:.3px}
.f-bar{position:absolute;top:84px;width:4px;height:30px;background:var(--accent)}
.f-head-rule{position:absolute;top:116px;width:54px;height:2px;background:var(--accent)}
.f-links{position:absolute;top:142px;list-style:none;font-size:13px;line-height:26px;letter-spacing:.3px;white-space:nowrap}
.f-item{position:absolute;left:140px;display:flex;gap:18px}
.f-item .ic{width:34px;height:34px;border-radius:50%;background:#1e2436;display:flex;align-items:center;justify-content:center}
.f-item small{display:block;font-size:12px;color:#b8bcc6}
.f-item p{font-size:13.5px;line-height:19px;white-space:nowrap}
.copy-bar{position:absolute;left:0;top:3906px;width:1200px;height:72px;background:var(--footer-bar);color:var(--white);font-size:14px;display:flex;align-items:center;justify-content:center}
.copy-bar a{color:var(--accent);text-decoration:underline;margin:0 3px}
.to-top{position:absolute;left:1113px;top:3883px;width:40px;height:40px;border-radius:6px;background:var(--accent);display:flex;align-items:center;justify-content:center}
</style>
</head>
<body>

<header class="site-header">
  <svg class="topbar" width="1200" height="38" viewBox="0 0 1200 38" aria-hidden="true">
    <polygon points="378,0 1200,0 1200,38 415,38" fill="#0a1a3c"/>
  </svg>
  <div class="top-mail">
    <span class="ic"><svg width="12" height="9" viewBox="0 0 12 9"><rect x="0.5" y="0.5" width="11" height="8" fill="none" stroke="#0a1a3c"/><path d="M0.5 0.5 6 5 11.5 0.5" fill="none" stroke="#0a1a3c"/></svg></span>
    hello@norvelletravel.example
  </div>
  <div class="top-phone">
    <span class="ic"><svg width="13" height="13" viewBox="0 0 24 24"><path fill="#fff" d="M6.6 10.8a15 15 0 0 0 6.6 6.6l2.2-2.2a1 1 0 0 1 1-.25 11.4 11.4 0 0 0 3.6.57 1 1 0 0 1 1 1V20a1 1 0 0 1-1 1A17 17 0 0 1 3 4a1 1 0 0 1 1-1h3.5a1 1 0 0 1 1 1c0 1.25.2 2.45.57 3.57a1 1 0 0 1-.25 1z"/></svg></span>
    Call or Text : +1 (555) 014 7788
  </div>
  <a class="brand" href="#"><span class="brand-dot"></span><span class="brand-name">NORVELLE TRAVEL</span></a>
  <nav>
    <a class="nav-link" href="#" style="left:385px;top:71px"><svg width="22" height="14" viewBox="0 0 22 14"><path d="M1 7h20M12 7 7 1M12 7 7 13M4 7 2 4M4 7 2 10" stroke="#0a1a3c" stroke-width="1.4" fill="none"/></svg>HOME</a>
    <a class="nav-link" href="#" style="left:488px">WHY CHOOSE NORVELLE TRAVEL?</a>
    <a class="nav-link" href="#" style="left:722px">TRAVEL MANAGEMENT SERVICES</a>
  </nav>
  <a class="nav-cta" href="#">CONTACT US <span>&#8250;</span></a>
</header>

<section class="hero">
  <svg width="1200" height="715" viewBox="0 0 1200 715" role="img" aria-label="Photo of yellow and silver suitcases beside a bright window overlooking the sea">
    <defs>
      <linearGradient id="heroSky" x1="0" y1="0" x2="0" y2="1">
        <stop offset="0" stop-color="#a9c7dc"/>
        <stop offset=".55" stop-color="#dfe9ef"/>
        <stop offset=".75" stop-color="#b4bcc2"/>
        <stop offset="1" stop-color="#8d9399"/>
      </linearGradient>
    </defs>
    <polygon points="0,0 1200,0 1200,576 600,668 0,576" fill="url(#heroSky)"/>
    <polygon points="30,599 600,668 1170,599 600,715" fill="#0a1a3c"/>
  </svg>
</section>
<h1 class="hero-title">NORVELLE TRAVEL</h1>
<p class="hero-sub">BUSINESS TRAVEL REINVENTED</p>
<a class="btn-outline" href="#" style="left:115px;top:447px;width:156px;height:42px">GET STARTED <span>&#8250;</span></a>
<span class="arrow-btn" style="left:24px;top:350px"><svg width="20" height="14" viewBox="0 0 20 14"><path d="M19 7H2M8 1 2 7l6 6" stroke="#0a1a3c" stroke-width="2" fill="none"/></svg></span>
<span class="arrow-btn" style="left:1117px;top:350px"><svg width="20" height="14" viewBox="0 0 20 14"><path d="M1 7h17M12 1l6 6-6 6" stroke="#0a1a3c" stroke-width="2" fill="none"/></svg></span>
<div class="dots"><span></span><span class="on"></span><span></span></div>

<section class="why">
  <div class="why-visual" role="img" aria-label="Photo of a smiling business traveller"></div>
  <h2 class="h-sec abs" style="left:613px;top:945px"><span class="light">Why Choose</span> Norvelle Travel?</h2>
  <div class="rule abs" style="left:615px;top:996px"><i style="width:64px"></i><b></b><i style="width:20px"></i></div>
  <p class="why-text">Norvelle Travel is a global leader in business travel management services. We drive savings, efficiency, and unparalleled service to businesses and their travelers all around the world. If you are looking for a tailored travel managed solution focused on offering white glove service and fulfilling your individual preferences ,while delivering customer excellence, you've come to the right place. At Norvelle Travel, our mission is to have you focus on your day to day business while we handle all of the logistics and details for the most successful all encompassing travel experience. From emergency passport arrangements to last minute cancellations, re-bookings, and other intricate travel challenges, Norvelle Travel is well versed in handling the routine array of travel services, as well as solving any travel related issue that might arise.</p>
  <a class="btn-solid" href="#" style="left:612px;top:1383px;width:147px;height:41px">LEARN MORE <span>&#8250;</span></a>
</section>

<section class="services">
  <h2 class="h-sec abs" style="left:0;width:1200px;top:72px;text-align:center"><span class="light">Travel Management</span> Services</h2>
  <div class="rule abs" style="left:522px;top:124px"><i style="width:66px"></i><b></b><i style="width:66px"></i></div>
</section>

<div class="svc-card" style="top:1683px"></div>
<h3 class="svc-title" style="left:300px;width:362px;top:1737px;text-align:right">Unparalled Service</h3>
<span class="under" style="left:608px;top:1776px"></span>
<p class="svc-text" style="left:202px;width:460px;top:1790px;text-align:justify;text-align-last:right">Norvelle Travel is famous for our concierge style approach to travel. From detailed planning, to commercial or private air travel, transportation, including car rentals, chauffers, busses for larger groups, hotels, all styles of lodging accomodations, special event planning and more, Norvelle Travel is like having your own personal or corporate travel butler.</p>
<span class="svc-ring" style="left:697px;top:1700px"></span>
<div class="svc-photo" style="left:701px;top:1711px;background:linear-gradient(150deg,#c9d3da,#8c7a5f 50%,#3d4f6a)" role="img" aria-label="Photo of a traveller with hat and backpack in a station"></div>

<div class="svc-card" style="top:2015px"></div>
<span class="svc-ring" style="left:163px;top:2032px"></span>
<div class="svc-photo" style="left:189px;top:2040px;background:radial-gradient(circle at 50% 40%,#e6eef2,#7fb6d6 55%,#2a6f9c)" role="img" aria-label="Illustration of world landmarks on a globe"></div>
<h3 class="svc-title" style="left:497px;top:2068px">Budget and Travel Spend Reporting</h3>
<span class="under" style="left:498px;top:2107px"></span>
<p class="svc-text" style="left:498px;width:460px;top:2120px;text-align:justify">Having a travel management service will ensure that your company enforces corporate compliance and maintains control over travel decisions. This ensures that your employees stick to your budget, which in turn will protect your bottom line. Travel expenses can be costly.</p>

<div class="svc-card" style="top:2344px"></div>
<h3 class="svc-title" style="left:300px;width:362px;top:2397px;text-align:right">Efficiency</h3>
<span class="under" style="left:608px;top:2436px"></span>
<p class="svc-text" style="left:202px;width:460px;top:2450px;text-align:justify;text-align-last:right">Time is your most valuable tool! Our goal at Norvelle Travel is to have your employees' complete focus be on your core business, while having us handle all the logistics for their travel. One of the most appreciated services we offer is the management of travel headaches. Unforeseen circumstances such as cancellations, missed flights, cancelled flights, last minute bookings or changed plans, can take hours to rectify.</p>
<span class="svc-ring" style="left:697px;top:2358px"></span>
<div class="svc-photo" style="left:701px;top:2367px;background:linear-gradient(150deg,#d6d9dc,#c7622e 50%,#3b4b63)" role="img" aria-label="Photo of a traveller pulling an orange suitcase"></div>

<a class="btn-solid" href="#" style="left:488px;top:2714px;width:224px;height:42px">VIEW MORE SERVICES <span>&#8250;</span></a>

<section class="contact">
  <svg width="1200" height="716" viewBox="0 0 1200 716" aria-hidden="true" style="position:absolute;left:0;top:0">
    <defs>
      <linearGradient id="contactPhoto" x1="0" y1="0" x2="1" y2="1">
        <stop offset="0" stop-color="#b7c3c9"/>
        <stop offset=".45" stop-color="#d4a24a"/>
        <stop offset="1" stop-color="#5e5246"/>
      </linearGradient>
    </defs>
    <polygon points="30,132 600,16 1170,132 600,55" fill="#0a1a3c"/>
    <polygon points="0,155 600,55 600,716 0,716" fill="url(#contactPhoto)"/>
    <polygon points="600,55 1200,155 1200,716 600,716" fill="#cfeaf8"/>
  </svg>
  <div role="img" aria-label="Photo of a happy traveller in a sun hat holding a phone" style="position:absolute;left:0;top:155px;width:600px;height:561px"></div>
</section>
<p class="c-kicker">Who We Are</p>
<h2 class="c-title">Contact Us</h2>
<div class="rule abs" style="left:708px;top:3037px"><i style="width:18px"></i><b style="background:var(--navy);width:22px"></b><i style="width:18px;background:var(--accent)"></i></div>
<p class="c-text">Saerspiciatis undeaslseio sepoepoiise omnisiste natusvoluptatem accusanl audantium.</p>
<div class="field" style="top:3117px">Your Name</div>
<div class="field" style="top:3173px">Email</div>
<div class="field" style="top:3230px">Phone Number</div>
<div class="field" style="top:3286px;height:156px">Write a message</div>
<a class="btn-outline" href="#" style="left:658px;top:3459px;width:121px;height:40px;background:transparent">SUBMIT <span>&#8250;</span></a>

<footer class="footer">
  <span class="f-div" style="left:116px"></span>
  <span class="f-div" style="left:493px"></span>
  <span class="f-div" style="left:761px"></span>
  <span class="f-div" style="left:970px"></span>

  <span class="f-bar" style="left:116px"></span>
  <h4 class="f-head" style="left:149px">CONTACT US</h4>
  <span class="f-head-rule" style="left:149px"></span>
  <div class="f-item" style="top:142px">
    <span class="ic"><svg width="14" height="18" viewBox="0 0 14 18"><path d="M7 0a7 7 0 0 0-7 7c0 5 7 11 7 11s7-6 7-11a7 7 0 0 0-7-7z" fill="#6cc7ef"/><circle cx="7" cy="7" r="2.6" fill="#1e2436"/></svg></span>
    <div><small>Address</small><p>1470 W Harlow Ave, Redfield<br>Texas, USA, 75001</p></div>
  </div>
  <div class="f-item" style="top:220px">
    <span class="ic"><svg width="15" height="15" viewBox="0 0 24 24"><path fill="#6cc7ef" d="M6.6 10.8a15 15 0 0 0 6.6 6.6l2.2-2.2a1 1 0 0 1 1-.25 11.4 11.4 0 0 0 3.6.57 1 1 0 0 1 1 1V20a1 1 0 0 1-1 1A17 17 0 0 1 3 4a1 1 0 0 1 1-1h3.5a1 1 0 0 1 1 1c0 1.25.2 2.45.57 3.57a1 1 0 0 1-.25 1z"/></svg></span>
    <div><small>Call Us</small><p>+1 (555) 014 7788</p></div>
  </div>
  <div class="f-item" style="top:274px">
    <span class="ic"><svg width="16" height="12" viewBox="0 0 16 12"><rect width="16" height="12" rx="1.5" fill="#6cc7ef"/><path d="M1 1.5 8 7l7-5.5" fill="none" stroke="#1e2436" stroke-width="1.4"/></svg></span>
    <div><small>Email</small><p>hello@norvelletravel.example</p></div>
  </div>

  <span class="f-bar" style="left:493px"></span>
  <h4 class="f-head" style="left:513px">QUICK LINKS</h4>
  <ul class="f-links" style="left:515px"><li>HOME</li><li>WHY CHOOSE NORVELLE TRAVEL?</li><li>TRAVEL MANAGEMENT SERVICES</li><li>CONTACT US</li></ul>

  <span class="f-bar" style="left:761px"></span>
  <h4 class="f-head" style="left:783px">LINKS</h4>
  <ul class="f-links" style="left:785px"><li>COPYRIGHT</li><li>LEGAL</li><li>PRIVACY</li><li>ACCESSIBILITY</li><li>SITEMAP</li></ul>

  <span class="f-bar" style="left:970px"></span>
  <h4 class="f-head" style="left:996px">SUPPORT</h4>
  <ul class="f-links" style="left:998px"><li>TEAM</li><li>ABOUT US</li><li>CAREERS</li><li>OUR VALUES</li></ul>
</footer>

<div class="copy-bar">©2023. <a href="#">Norvelle Travel</a>. All rights reserved.</div>
<a class="to-top" href="#"><svg width="14" height="9" viewBox="0 0 14 9"><path d="M1 8l6-6 6 6" stroke="#0a1a3c" stroke-width="2" fill="none"/></svg></a>

</body>
</html>
```